Step and Repeat Backdrop for wedding reception photo booth

Would like to have a Step and Repeat Backdrop (8 foot high by 10 foot wide) that incorporates the wedding logo (attached) and the names Helen and Gavin. Background should be white, and wedding colors are burgundy and gold. Show me creativity :-) I have included some random samples.

```html
<!DOCTYPE html>
<html lang="en">
<head>
<meta charset="utf-8">
<title>Helen &amp; Gavin — Step and Repeat Backdrop</title>
<link rel="stylesheet" href="https://fonts.googleapis.com/css2?family=Playfair+Display:wght@400&display=swap">
<style>
  :root {
    --burgundy: #7d0022;
    --gold: #8c7612;
    --white: #ffffff;
    --stage: #eceef1;
    --serif: "Playfair Display", Georgia, serif;
  }
  * { box-sizing: border-box; margin: 0; padding: 0; }
  html, body { width: 1200px; height: 1200px; overflow: hidden; background: var(--stage); }
  .canvas { position: relative; width: 1200px; height: 1200px; }
  .backdrop {
    position: absolute; left: 30px; top: 125px;
    width: 1140px; height: 951px;
    background: var(--white);
    display: grid;
    grid-template-columns: repeat(10, 110px);
    grid-template-rows: repeat(11, 81px);
    padding: 31px 19px 29px 21px;
  }
  .tile {
    display: flex; flex-direction: column; align-items: center; justify-content: center;
    gap: 3px;
  }
  .tile--gold { color: var(--gold); }
  .tile--burgundy { color: var(--burgundy); }
  .flourish {
    display: block; width: 52px; height: 8px; border-radius: 4px;
    background: currentColor; opacity: .28;
  }
  .monogram {
    font-family: var(--serif); font-weight: 400; font-size: 24px; line-height: 1;
    letter-spacing: -1px;
  }
  .feature {
    grid-column: 4 / 8; grid-row: 5 / 9;
    justify-self: center; align-self: center;
    position: relative; width: 391px; height: 299px;
    background: linear-gradient(to bottom, var(--burgundy) 0%, var(--burgundy) 44%, var(--gold) 52%, var(--gold) 100%);
    box-shadow: 0 0 6px 2px rgba(140, 80, 40, .35);
  }
  .feature__frame {
    position: absolute; inset: 16px 18px;
    border: 2px solid var(--white);
    display: flex; flex-direction: column; align-items: center; justify-content: center;
    gap: 14px;
  }
  .feature__flourish {
    display: block; width: 270px; height: 44px; border-radius: 22px;
    background: rgba(255, 255, 255, .22);
  }
  .feature__monogram {
    font-family: var(--serif); font-weight: 400; font-size: 104px; line-height: .9;
    color: var(--white); letter-spacing: -4px;
  }
</style>
</head>
<body>
<main class="canvas">
  <section class="backdrop" aria-label="Helen and Gavin step and repeat backdrop">
    <div class="feature">
      <div class="feature__frame">
        <span class="feature__flourish" role="img" aria-label="White ornamental scroll flourish"></span>
        <span class="feature__monogram">H&amp;G</span>
        <span class="feature__flourish" role="img" aria-label="White ornamental scroll flourish"></span>
      </div>
    </div>

    <!-- row 1 -->
    <div class="tile tile--gold"><span class="flourish" role="img" aria-label="Scroll flourish"></span><span class="monogram">H&amp;G</span><span class="flourish" role="img" aria-label="Scroll flourish"></span></div>
    <div class="tile tile--burgundy"><span class="flourish" role="img" aria-label="Scroll flourish"></span><span class="monogram">H&amp;G</span><span class="flourish" role="img" aria-label="Scroll flourish"></span></div>
    <div class="tile tile--gold"><span class="flourish" role="img" aria-label="Scroll flourish"></span><span class="monogram">H&amp;G</span><span class="flourish" role="img" aria-label="Scroll flourish"></span></div>
    <div class="tile tile--burgundy"><span class="flourish" role="img" aria-label="Scroll flourish"></span><span class="monogram">H&amp;G</span><span class="flourish" role="img" aria-label="Scroll flourish"></span></div>
    <div class="tile tile--gold"><span class="flourish" role="img" aria-label="Scroll flourish"></span><span class="monogram">H&amp;G</span><span class="flourish" role="img" aria-label="Scroll flourish"></span></div>
    <div class="tile tile--burgundy"><span class="flourish" role="img" aria-label="Scroll flourish"></span><span class="monogram">H&amp;G</span><span class="flourish" role="img" aria-label="Scroll flourish"></span></div>
    <div class="tile tile--gold"><span class="flourish" role="img" aria-label="Scroll flourish"></span><span class="monogram">H&amp;G</span><span class="flourish" role="img" aria-label="Scroll flourish"></span></div>
    <div class="tile tile--burgundy"><span class="flourish" role="img" aria-label="Scroll flourish"></span><span class="monogram">H&amp;G</span><span class="flourish" role="img" aria-label="Scroll flourish"></span></div>
    <div class="tile tile--gold"><span class="flourish" role="img" aria-label="Scroll flourish"></span><span class="monogram">H&amp;G</span><span class="flourish" role="img" aria-label="Scroll flourish"></span></div>
    <div class="tile tile--burgundy"><span class="flourish" role="img" aria-label="Scroll flourish"></span><span class="monogram">H&amp;G</span><span class="flourish" role="img" aria-label="Scroll flourish"></span></div>

    <!-- row 2 -->
    <div class="tile tile--burgundy"><span class="flourish" role="img" aria-label="Scroll flourish"></span><span class="monogram">H&amp;G</span><span class="flourish" role="img" aria-label="Scroll flourish"></span></div>
    <div class="tile tile--gold"><span class="flourish" role="img" aria-label="Scroll flourish"></span><span class="monogram">H&amp;G</span><span class="flourish" role="img" aria-label="Scroll flourish"></span></div>
    <div class="tile tile--burgundy"><span class="flourish" role="img" aria-label="Scroll flourish"></span><span class="monogram">H&amp;G</span><span class="flourish" role="img" aria-label="Scroll flourish"></span></div>
    <div class="tile tile--gold"><span class="flourish" role="img" aria-label="Scroll flourish"></span><span class="monogram">H&amp;G</span><span class="flourish" role="img" aria-label="Scroll flourish"></span></div>
    <div class="tile tile--burgundy"><span class="flourish" role="img" aria-label="Scroll flourish"></span><span class="monogram">H&amp;G</span><span class="flourish" role="img" aria-label="Scroll flourish"></span></div>
    <div class="tile tile--gold"><span class="flourish" role="img" aria-label="Scroll flourish"></span><span class="monogram">H&amp;G</span><span class="flourish" role="img" aria-label="Scroll flourish"></span></div>
    <div class="tile tile--burgundy"><span class="flourish" role="img" aria-label="Scroll flourish"></span><span class="monogram">H&amp;G</span><span class="flourish" role="img" aria-label="Scroll flourish"></span></div>
    <div class="tile tile--gold"><span class="flourish" role="img" aria-label="Scroll flourish"></span><span class="monogram">H&amp;G</span><span class="flourish" role="img" aria-label="Scroll flourish"></span></div>
    <div class="tile tile--burgundy"><span class="flourish" role="img" aria-label="Scroll flourish"></span><span class="monogram">H&amp;G</span><span class="flourish" role="img" aria-label="Scroll flourish"></span></div>
    <div class="tile tile--gold"><span class="flourish" role="img" aria-label="Scroll flourish"></span><span class="monogram">H&amp;G</span><span class="flourish" role="img" aria-label="Scroll flourish"></span></div>

    <!-- row 3 -->
    <div class="tile tile--gold"><span class="flourish" role="img" aria-label="Scroll flourish"></span><span class="monogram">H&amp;G</span><span class="flourish" role="img" aria-label="Scroll flourish"></span></div>
    <div class="tile tile--burgundy"><span class="flourish" role="img" aria-label="Scroll flourish"></span><span class="monogram">H&amp;G</span><span class="flourish" role="img" aria-label="Scroll flourish"></span></div>
    <div class="tile tile--gold"><span class="flourish" role="img" aria-label="Scroll flourish"></span><span class="monogram">H&amp;G</span><span class="flourish" role="img" aria-label="Scroll flourish"></span></div>
    <div class="tile tile--burgundy"><span class="flourish" role="img" aria-label="Scroll flourish"></span><span class="monogram">H&amp;G</span><span class="flourish" role="img" aria-label="Scroll flourish"></span></div>
    <div class="tile tile--gold"><span class="flourish" role="img" aria-label="Scroll flourish"></span><span class="monogram">H&amp;G</span><span class="flourish" role="img" aria-label="Scroll flourish"></span></div>
    <div class="tile tile--burgundy"><span class="flourish" role="img" aria-label="Scroll flourish"></span><span class="monogram">H&amp;G</span><span class="flourish" role="img" aria-label="Scroll flourish"></span></div>
    <div class="tile tile--gold"><span class="flourish" role="img" aria-label="Scroll flourish"></span><span class="monogram">H&amp;G</span><span class="flourish" role="img" aria-label="Scroll flourish"></span></div>
    <div class="tile tile--burgundy"><span class="flourish" role="img" aria-label="Scroll flourish"></span><span class="monogram">H&amp;G</span><span class="flourish" role="img" aria-label="Scroll flourish"></span></div>
    <div class="tile tile--gold"><span class="flourish" role="img" aria-label="Scroll flourish"></span><span class="monogram">H&amp;G</span><span class="flourish" role="img" aria-label="Scroll flourish"></span></div>
    <div class="tile tile--burgundy"><span class="flourish" role="img" aria-label="Scroll flourish"></span><span class="monogram">H&amp;G</span><span class="flourish" role="img" aria-label="Scroll flourish"></span></div>

    <!-- row 4 -->
    <div class="tile tile--burgundy"><span class="flourish" role="img" aria-label="Scroll flourish"></span><span class="monogram">H&amp;G</span><span class="flourish" role="img" aria-label="Scroll flourish"></span></div>
    <div class="tile tile--gold"><span class="flourish" role="img" aria-label="Scroll flourish"></span><span class="monogram">H&amp;G</span><span class="flourish" role="img" aria-label="Scroll flourish"></span></div>
    <div class="tile tile--burgundy"><span class="flourish" role="img" aria-label="Scroll flourish"></span><span class="monogram">H&amp;G</span><span class="flourish" role="img" aria-label="Scroll flourish"></span></div>
    <div class="tile tile--gold"><span class="flourish" role="img" aria-label="Scroll flourish"></span><span class="monogram">H&amp;G</span><span class="flourish" role="img" aria-label="Scroll flourish"></span></div>
    <div class="tile tile--burgundy"><span class="flourish" role="img" aria-label="Scroll flourish"></span><span class="monogram">H&amp;G</span><span class="flourish" role="img" aria-label="Scroll flourish"></span></div>
    <div class="tile tile--gold"><span class="flourish" role="img" aria-label="Scroll flourish"></span><span class="monogram">H&amp;G</span><span class="flourish" role="img" aria-label="Scroll flourish"></span></div>
    <div class="tile tile--burgundy"><span class="flourish" role="img" aria-label="Scroll flourish"></span><span class="monogram">H&amp;G</span><span class="flourish" role="img" aria-label="Scroll flourish"></span></div>
    <div class="tile tile--gold"><span class="flourish" role="img" aria-label="Scroll flourish"></span><span class="monogram">H&amp;G</span><span class="flourish" role="img" aria-label="Scroll flourish"></span></div>
    <div class="tile tile--burgundy"><span class="flourish" role="img" aria-label="Scroll flourish"></span><span class="monogram">H&amp;G</span><span class="flourish" role="img" aria-label="Scroll flourish"></span></div>
    <div class="tile tile--gold"><span class="flourish" role="img" aria-label="Scroll flourish"></span><span class="monogram">H&amp;G</span><span class="flourish" role="img" aria-label="Scroll flourish"></span></div>

    <!-- row 5 -->
    <div class="tile tile--gold"><span class="flourish" role="img" aria-label="Scroll flourish"></span><span class="monogram">H&amp;G</span><span class="flourish" role="img" aria-label="Scroll flourish"></span></div>
    <div class="tile tile--burgundy"><span class="flourish" role="img" aria-label="Scroll flourish"></span><span class="monogram">H&amp;G</span><span class="flourish" role="img" aria-label="Scroll flourish"></span></div>
    <div class="tile tile--gold"><span class="flourish" role="img" aria-label="Scroll flourish"></span><span class="monogram">H&amp;G</span><span class="flourish" role="img" aria-label="Scroll flourish"></span></div>
    <div class="tile tile--burgundy"><span class="flourish" role="img" aria-label="Scroll flourish"></span><span class="monogram">H&amp;G</span><span class="flourish" role="img" aria-label="Scroll flourish"></span></div>
    <div class="tile tile--gold"><span class="flourish" role="img" aria-label="Scroll flourish"></span><span class="monogram">H&amp;G</span><span class="flourish" role="img" aria-label="Scroll flourish"></span></div>
    <div class="tile tile--burgundy"><span class="flourish" role="img" aria-label="Scroll flourish"></span><span class="monogram">H&amp;G</span><span class="flourish" role="img" aria-label="Scroll flourish"></span></div>

    <!-- row 6 -->
    <div class="tile tile--burgundy"><span class="flourish" role="img" aria-label="Scroll flourish"></span><span class="monogram">H&amp;G</span><span class="flourish" role="img" aria-label="Scroll flourish"></span></div>
    <div class="tile tile--gold"><span class="flourish" role="img" aria-label="Scroll flourish"></span><span class="monogram">H&amp;G</span><span class="flourish" role="img" aria-label="Scroll flourish"></span></div>
    <div class="tile tile--burgundy"><span class="flourish" role="img" aria-label="Scroll flourish"></span><span class="monogram">H&amp;G</span><span class="flourish" role="img" aria-label="Scroll flourish"></span></div>
    <div class="tile tile--gold"><span class="flourish" role="img" aria-label="Scroll flourish"></span><span class="monogram">H&amp;G</span><span class="flourish" role="img" aria-label="Scroll flourish"></span></div>
    <div class="tile tile--burgundy"><span class="flourish" role="img" aria-label="Scroll flourish"></span><span class="monogram">H&amp;G</span><span class="flourish" role="img" aria-label="Scroll flourish"></span></div>
    <div class="tile tile--gold"><span class="flourish" role="img" aria-label="Scroll flourish"></span><span class="monogram">H&amp;G</span><span class="flourish" role="img" aria-label="Scroll flourish"></span></div>

    <!-- row 7 -->
    <div class="tile tile--gold"><span class="flourish" role="img" aria-label="Scroll flourish"></span><span class="monogram">H&amp;G</span><span class="flourish" role="img" aria-label="Scroll flourish"></span></div>
    <div class="tile tile--burgundy"><span class="flourish" role="img" aria-label="Scroll flourish"></span><span class="monogram">H&amp;G</span><span class="flourish" role="img" aria-label="Scroll flourish"></span></div>
    <div class="tile tile--gold"><span class="flourish" role="img" aria-label="Scroll flourish"></span><span class="monogram">H&amp;G</span><span class="flourish" role="img" aria-label="Scroll flourish"></span></div>
    <div class="tile tile--burgundy"><span class="flourish" role="img" aria-label="Scroll flourish"></span><span class="monogram">H&amp;G</span><span class="flourish" role="img" aria-label="Scroll flourish"></span></div>
    <div class="tile tile--gold"><span class="flourish" role="img" aria-label="Scroll flourish"></span><span class="monogram">H&amp;G</span><span class="flourish" role="img" aria-label="Scroll flourish"></span></div>
    <div class="tile tile--burgundy"><span class="flourish" role="img" aria-label="Scroll flourish"></span><span class="monogram">H&amp;G</span><span class="flourish" role="img" aria-label="Scroll flourish"></span></div>

    <!-- row 8 -->
    <div class="tile tile--burgundy"><span class="flourish" role="img" aria-label="Scroll flourish"></span><span class="monogram">H&amp;G</span><span class="flourish" role="img" aria-label="Scroll flourish"></span></div>
    <div class="tile tile--gold"><span class="flourish" role="img" aria-label="Scroll flourish"></span><span class="monogram">H&amp;G</span><span class="flourish" role="img" aria-label="Scroll flourish"></span></div>
    <div class="tile tile--burgundy"><span class="flourish" role="img" aria-label="Scroll flourish"></span><span class="monogram">H&amp;G</span><span class="flourish" role="img" aria-label="Scroll flourish"></span></div>
    <div class="tile tile--gold"><span class="flourish" role="img" aria-label="Scroll flourish"></span><span class="monogram">H&amp;G</span><span class="flourish" role="img" aria-label="Scroll flourish"></span></div>
    <div class="tile tile--burgundy"><span class="flourish" role="img" aria-label="Scroll flourish"></span><span class="monogram">H&amp;G</span><span class="flourish" role="img" aria-label="Scroll flourish"></span></div>
    <div class="tile tile--gold"><span class="flourish" role="img" aria-label="Scroll flourish"></span><span class="monogram">H&amp;G</span><span class="flourish" role="img" aria-label="Scroll flourish"></span></div>

    <!-- row 9 -->
    <div class="tile tile--gold"><span class="flourish" role="img" aria-label="Scroll flourish"></span><span class="monogram">H&amp;G</span><span class="flourish" role="img" aria-label="Scroll flourish"></span></div>
    <div class="tile tile--burgundy"><span class="flourish" role="img" aria-label="Scroll flourish"></span><span class="monogram">H&amp;G</span><span class="flourish" role="img" aria-label="Scroll flourish"></span></div>
    <div class="tile tile--gold"><span class="flourish" role="img" aria-label="Scroll flourish"></span><span class="monogram">H&amp;G</span><span class="flourish" role="img" aria-label="Scroll flourish"></span></div>
    <div class="tile tile--burgundy"><span class="flourish" role="img" aria-label="Scroll flourish"></span><span class="monogram">H&amp;G</span><span class="flourish" role="img" aria-label="Scroll flourish"></span></div>
    <div class="tile tile--gold"><span class="flourish" role="img" aria-label="Scroll flourish"></span><span class="monogram">H&amp;G</span><span class="flourish" role="img" aria-label="Scroll flourish"></span></div>
    <div class="tile tile--burgundy"><span class="flourish" role="img" aria-label="Scroll flourish"></span><span class="monogram">H&amp;G</span><span class="flourish" role="img" aria-label="Scroll flourish"></span></div>
    <div class="tile tile--gold"><span class="flourish" role="img" aria-label="Scroll flourish"></span><span class="monogram">H&amp;G</span><span class="flourish" role="img" aria-label="Scroll flourish"></span></div>
    <div class="tile tile--burgundy"><span class="flourish" role="img" aria-label="Scroll flourish"></span><span class="monogram">H&amp;G</span><span class="flourish" role="img" aria-label="Scroll flourish"></span></div>
    <div class="tile tile--gold"><span class="flourish" role="img" aria-label="Scroll flourish"></span><span class="monogram">H&amp;G</span><span class="flourish" role="img" aria-label="Scroll flourish"></span></div>
    <div class="tile tile--burgundy"><span class="flourish" role="img" aria-label="Scroll flourish"></span><span class="monogram">H&amp;G</span><span class="flourish" role="img" aria-label="Scroll flourish"></span></div>

    <!-- row 10 -->
    <div class="tile tile--burgundy"><span class="flourish" role="img" aria-label="Scroll flourish"></span><span class="monogram">H&amp;G</span><span class="flourish" role="img" aria-label="Scroll flourish"></span></div>
    <div class="tile tile--gold"><span class="flourish" role="img" aria-label="Scroll flourish"></span><span class="monogram">H&amp;G</span><span class="flourish" role="img" aria-label="Scroll flourish"></span></div>
    <div class="tile tile--burgundy"><span class="flourish" role="img" aria-label="Scroll flourish"></span><span class="monogram">H&amp;G</span><span class="flourish" role="img" aria-label="Scroll flourish"></span></div>
    <div class="tile tile--gold"><span class="flourish" role="img" aria-label="Scroll flourish"></span><span class="monogram">H&amp;G</span><span class="flourish" role="img" aria-label="Scroll flourish"></span></div>
    <div class="tile tile--burgundy"><span class="flourish" role="img" aria-label="Scroll flourish"></span><span class="monogram">H&amp;G</span><span class="flourish" role="img" aria-label="Scroll flourish"></span></div>
    <div class="tile tile--gold"><span class="flourish" role="img" aria-label="Scroll flourish"></span><span class="monogram">H&amp;G</span><span class="flourish" role="img" aria-label="Scroll flourish"></span></div>
    <div class="tile tile--burgundy"><span class="flourish" role="img" aria-label="Scroll flourish"></span><span class="monogram">H&amp;G</span><span class="flourish" role="img" aria-label="Scroll flourish"></span></div>
    <div class="tile tile--gold"><span class="flourish" role="img" aria-label="Scroll flourish"></span><span class="monogram">H&amp;G</span><span class="flourish" role="img" aria-label="Scroll flourish"></span></div>
    <div class="tile tile--burgundy"><span class="flourish" role="img" aria-label="Scroll flourish"></span><span class="monogram">H&amp;G</span><span class="flourish" role="img" aria-label="Scroll flourish"></span></div>
    <div class="tile tile--gold"><span class="flourish" role="img" aria-label="Scroll flourish"></span><span class="monogram">H&amp;G</span><span class="flourish" role="img" aria-label="Scroll flourish"></span></div>

    <!-- row 11 -->
    <div class="tile tile--gold"><span class="flourish" role="img" aria-label="Scroll flourish"></span><span class="monogram">H&amp;G</span><span class="flourish" role="img" aria-label="Scroll flourish"></span></div>
    <div class="tile tile--burgundy"><span class="flourish" role="img" aria-label="Scroll flourish"></span><span class="monogram">H&amp;G</span><span class="flourish" role="img" aria-label="Scroll flourish"></span></div>
    <div class="tile tile--gold"><span class="flourish" role="img" aria-label="Scroll flourish"></span><span class="monogram">H&amp;G</span><span class="flourish" role="img" aria-label="Scroll flourish"></span></div>
    <div class="tile tile--burgundy"><span class="flourish" role="img" aria-label="Scroll flourish"></span><span class="monogram">H&amp;G</span><span class="flourish" role="img" aria-label="Scroll flourish"></span></div>
    <div class="tile tile--gold"><span class="flourish" role="img" aria-label="Scroll flourish"></span><span class="monogram">H&amp;G</span><span class="flourish" role="img" aria-label="Scroll flourish"></span></div>
    <div class="tile tile--burgundy"><span class="flourish" role="img" aria-label="Scroll flourish"></span><span class="monogram">H&amp;G</span><span class="flourish" role="img" aria-label="Scroll flourish"></span></div>
    <div class="tile tile--gold"><span class="flourish" role="img" aria-label="Scroll flourish"></span><span class="monogram">H&amp;G</span><span class="flourish" role="img" aria-label="Scroll flourish"></span></div>
    <div class="tile tile--burgundy"><span class="flourish" role="img" aria-label="Scroll flourish"></span><span class="monogram">H&amp;G</span><span class="flourish" role="img" aria-label="Scroll flourish"></span></div>
    <div class="tile tile--gold"><span class="flourish" role="img" aria-label="Scroll flourish"></span><span class="monogram">H&amp;G</span><span class="flourish" role="img" aria-label="Scroll flourish"></span></div>
    <div class="tile tile--burgundy"><span class="flourish" role="img" aria-label="Scroll flourish"></span><span class="monogram">H&amp;G</span><span class="flourish" role="img" aria-label="Scroll flourish"></span></div>
  </section>
</main>
</body>
</html>
```